We (R. T. Galvin & Partners, Inc.) are an executive Search firm based in Los Angeles that is exclusively focused in the Med Tech and Health Tech arenas.   I need a logo to communicate that we are a high end search firm, but also that we are focused in the medicine and science arenas called health tech and med tech.  Many of our clients have robotics and artificial intelligence type products, so it is very technology forward.  I tend to gravitate towards clean, sharp aesthetic as opposed to something that is really over the top.
Attached are files with my logo in two different layouts.  In addition to the letterhead and envelope, I also will need an electronic letterhead in Microsoft Word.  I tend to
I look forward to seeing the designs and just let me know if you have any questions.
Dale

```html
<!DOCTYPE html>
<html lang="en">
<head>
<meta charset="utf-8">
<title>R. T. Galvin &amp; Partners, Inc. — Stationery</title>
<link href="https://fonts.googleapis.com/css2?family=Source+Sans+3:wght@400;600&display=swap" rel="stylesheet">
<style>
  :root {
    --bg: #e3e3e3;
    --paper: #f3f4f6;
    --ink: #2b2b2b;
    --ink-soft: #4a4a4a;
    --accent: #4a9bd6;
    --night: #2b2b2b;
    --night-flap: #222222;
    --on-night: #f2f2f2;
  }
  * { box-sizing: border-box; margin: 0; padding: 0; }
  html, body { width: 1200px; height: 882px; overflow: hidden; }
  body {
    background: var(--bg);
    font-family: "Source Sans 3", "Helvetica Neue", Arial, sans-serif;
    color: var(--ink);
    position: relative;
  }

  /* Brand lockup */
  .brand { position: absolute; display: flex; align-items: center; gap: 8px; }
  .brand-dot { width: 22px; height: 22px; border-radius: 50%; background: var(--accent); flex: none; }
  .brand-name { font-weight: 600; font-size: 12.5px; line-height: 1.15; color: var(--ink); }
  .on-night .brand-name { color: var(--on-night); }

  /* Contact block */
  .contact { position: absolute; font-size: 8px; line-height: 10px; color: var(--ink); }
  .on-night .contact { color: var(--on-night); }
  .contact .firm, .contact .web { color: var(--accent); }
  .contact .gap { height: 6px; }
  .contact .web { margin-top: 5px; }
  .contact .row { display: flex; align-items: center; gap: 3px; }
  .contact svg { width: 7px; height: 7px; fill: var(--accent); flex: none; }

  /* Letterhead */
  .letterhead {
    position: absolute; left: 93px; top: 80px; width: 499px; height: 704px;
    background: var(--paper);
  }
  .letterhead .brand { left: 47px; top: 62px; }
  .letterhead .contact { left: 306px; top: 46px; }
  .letter-date { position: absolute; left: 48px; top: 177px; font-size: 9px; }
  .letter-recipient { position: absolute; left: 48px; top: 215px; font-size: 9px; line-height: 12px; }
  .letter-body {
    position: absolute; left: 47px; top: 284px; width: 403px;
    font-size: 7.2px; line-height: 12px; color: var(--ink-soft); text-align: justify;
  }
  .letter-body p + p { margin-top: 12px; }
  .signature-area { position: absolute; left: 358px; top: 528px; width: 82px; height: 28px; background: #e8e9ec; }
  .signer-title { position: absolute; left: 378px; top: 561px; font-size: 8px; color: var(--ink-soft); }

  /* Envelopes */
  .envelope { position: absolute; left: 646px; width: 472px; height: 283px; }
  .envelope-light { top: 160px; }
  .envelope-dark { top: 502px; }
  .envelope .flap { position: absolute; left: 0; top: 0; width: 472px; height: 68px; }
  .envelope .face { position: absolute; left: 0; top: 68px; width: 472px; height: 215px; }
  .envelope-light .face { background: var(--paper); }
  .envelope-dark .face { background: var(--night); }
  .envelope-light .flap path { fill: var(--accent); }
  .envelope-dark .flap path { fill: var(--night-flap); }
  .envelope .brand { left: 31px; top: 95px; }
  .envelope .contact { left: 28px; top: 185px; }
</style>
</head>
<body>

<svg width="0" height="0" style="position:absolute">
  <defs>
    <symbol id="icon-phone" viewBox="0 0 10 10"><path d="M2.2 0.6 3.6 2.6 2.8 3.6c.6 1.4 1.6 2.4 3 3l1-.8 2 1.4-.8 1.8C4.6 8.8 1.2 5.4.4 1.4z"/></symbol>
    <symbol id="icon-fax" viewBox="0 0 10 10"><path d="M2.5 1h5v2.5h-5zM1 4h8v4H7.5V6.5h-5V8H1zM3 7h4v2H3z"/></symbol>
    <symbol id="icon-mail" viewBox="0 0 10 10"><path d="M.5 2h9v6h-9zM1 2.6v.4l4 2.6 4-2.6v-.4z" fill-rule="evenodd"/></symbol>
  </defs>
</svg>

<!-- Letterhead -->
<section class="letterhead">
  <div class="brand">
    <span class="brand-dot"></span>
    <span class="brand-name">R. T. Galvin &amp; Partners, Inc.</span>
  </div>
  <div class="contact">
    <div class="firm">R. T. Galvin &amp; Partners Inc.</div>
    <div>412 Larkspur Avenue</div>
    <div>Pasadena, California 91105</div>
    <div class="gap"></div>
    <div class="row"><svg><use href="#icon-phone"/></svg>555-018-2740 <svg><use href="#icon-fax"/></svg>555-018-2741</div>
    <div class="row"><svg><use href="#icon-mail"/></svg>hello@rtgalvinpartners.com</div>
    <div class="web">rtgalvinpartners.com</div>
  </div>

  <div class="letter-date">Los Angeles, October 12, 2015</div>
  <div class="letter-recipient">
    Sr.<br>MARCO ALVAREZ<br>Web Master<br>City
  </div>

  <div class="letter-body">
    <p>Contrary to popular belief, Lorem Ipsum is not simply random text. It has roots in a piece of classical Latin literature from 45 BC, making it over 2000 years old. Howard Lindqvist, a Latin professor at Brackett Hill College in Vermont, looked up one of the more obscure Latin words, consectetur, from a Lorem Ipsum passage, and going through the cites of the word in classical literature,</p>
    <p>discovered the undoubtable source. Lorem Ipsum comes from sections 1.10.32 and 1.10.33 of "de Finibus Bonorum et Malorum" (The Extremes of Good and Evil), written in 45 BC. This book is a treatise on the theory of ethics, very popular during the Renaissance. The first line of Lorem Ipsum, "Lorem ipsum dolor sit amet..", comes from a line in section 1.10.32.</p>
    <p>The standard chunk of Lorem Ipsum used since the 1500s is reproduced below for those interested. Sections 1.10.32 and 1.10.33 from "de Finibus Bonorum et Malorum" are also reproduced in their exact original form, accompanied by English versions from the 1914 translation by E. Thornbury.</p>
    <p>There are many variations of passages of Lorem Ipsum available, but the majority have suffered alteration in some form, by injected humour, or randomised words which don't look even slightly believable. If you are going to use a passage of Lorem Ipsum, you need to be sure there isn't anything embarrassing hidden in the middle of text. All the Lorem Ipsum generators o</p>
  </div>

  <div class="signature-area" role="img" aria-label="Handwritten signature of the founder"></div>
  <div class="signer-title">CEO/ FOUNDER</div>
</section>

<!-- Light envelope -->
<section class="envelope envelope-light">
  <svg class="flap" viewBox="0 0 472 68"><path d="M0 68 L10 16 Q14 0 32 0 L440 0 Q458 0 462 16 L472 68 Z"/></svg>
  <div class="face"></div>
  <div class="brand">
    <span class="brand-dot"></span>
    <span class="brand-name">R. T. Galvin &amp; Partners, Inc.</span>
  </div>
  <div class="contact">
    <div class="firm">R. T. Galvin &amp; Partners Inc.</div>
    <div>412 Larkspur Avenue</div>
    <div>Pasadena, California 91105</div>
    <div class="gap"></div>
    <div class="row"><svg><use href="#icon-phone"/></svg>555-018-2740 <svg><use href="#icon-fax"/></svg>555-018-2741</div>
    <div class="row"><svg><use href="#icon-mail"/></svg>hello@rtgalvinpartners.com</div>
    <div class="web">rtgalvinpartners.com</div>
  </div>
</section>

<!-- Dark envelope -->
<section class="envelope envelope-dark on-night">
  <svg class="flap" viewBox="0 0 472 68"><path d="M0 68 L10 16 Q14 0 32 0 L440 0 Q458 0 462 16 L472 68 Z"/></svg>
  <div class="face"></div>
  <div class="brand">
    <span class="brand-dot"></span>
    <span class="brand-name">R. T. Galvin &amp; Partners, Inc.</span>
  </div>
  <div class="contact">
    <div class="firm">R. T. Galvin &amp; Partners Inc.</div>
    <div>412 Larkspur Avenue</div>
    <div>Pasadena, California 91105</div>
    <div class="gap"></div>
    <div class="row"><svg><use href="#icon-phone"/></svg>555-018-2740 <svg><use href="#icon-fax"/></svg>555-018-2741</div>
    <div class="row"><svg><use href="#icon-mail"/></svg>hello@rtgalvinpartners.com</div>
    <div class="web">rtgalvinpartners.com</div>
  </div>
</section>

</body>
</html>
```